New Business Cards for Tormin Group

We need a new Business Card to compliment our new logo. We are a vibrant design, manufacture and install business providing recreation areas, public parks and Municipal spaces. We want business cards that are classy, modern and clean.

We have recently changed our logo, and are celebrating our 40th anniversary. We want business cards with a new modern design to reflect our status.

Target Market(s)

Customers

Contact Information for Business Card

We need all the details of our 3 offices as per the business card attached. Please disregard the old logo on the business card, the other three files show our new logo.

Requirements
Must have
• All info as per attached business card but with new logo.
Nice to have

```html
<!DOCTYPE html>
<html lang="en">
<head>
<meta charset="utf-8">
<title>Tormin Group Business Card</title>
<link href="https://fonts.googleapis.com/css2?family=Barlow:wght@400;600&display=swap" rel="stylesheet">
<style>
  :root {
    --brand-red: #e8262f;
    --ink: #3c3c3c;
    --ink-soft: #555555;
    --rule: #4a4a4a;
    --card: #ffffff;
    --backdrop: #d9d9d9;
  }
  html, body {
    margin: 0;
    width: 1200px;
    height: 800px;
    overflow: hidden;
    background: var(--backdrop);
    font-family: "Barlow", Arial, sans-serif;
  }
  .business-card {
    position: absolute;
    left: 100px;
    top: 116px;
    width: 1000px;
    height: 568px;
    background: var(--card);
    color: var(--ink);
  }
  .brand-mark {
    position: absolute;
    right: 68px;
    top: 88px;
    display: flex;
    align-items: center;
    gap: 14px;
    font-weight: 600;
    font-size: 46px;
    color: var(--ink);
    letter-spacing: 0.5px;
  }
  .brand-dot {
    width: 54px;
    height: 54px;
    border-radius: 50%;
    background: var(--brand-red);
  }
  .person {
    position: absolute;
    left: 48px;
    top: 240px;
    display: flex;
    align-items: baseline;
  }
  .person-name {
    font-weight: 600;
    font-size: 37px;
    color: var(--brand-red);
  }
  .person-dash {
    font-weight: 600;
    font-size: 30px;
    color: var(--brand-red);
    margin: 0 8px 0 12px;
  }
  .person-title {
    font-size: 24px;
    color: var(--ink);
  }
  .person-contact {
    position: absolute;
    left: 46px;
    top: 290px;
    font-size: 21px;
    color: var(--ink-soft);
    letter-spacing: 0.3px;
  }
  .divider {
    position: absolute;
    left: 48px;
    right: 48px;
    top: 336px;
    border-top: 1px solid var(--rule);
  }
  .office {
    position: absolute;
    top: 362px;
    font-size: 22px;
    color: var(--ink-soft);
  }
  .office--head { left: 52px; }
  .office--dubai { left: 373px; }
  .office--qatar { left: 692px; }
  .office-title {
    font-weight: 600;
    font-size: 23px;
    color: var(--brand-red);
    margin: 0 0 10px;
  }
  .office-address { margin: 0 0 6px; }
  .office-line {
    display: flex;
    align-items: center;
    gap: 12px;
    height: 30px;
  }
  .office-icon {
    width: 20px;
    height: 20px;
    fill: var(--brand-red);
    flex: none;
  }
</style>
</head>
<body>
<div class="business-card">
  <div class="brand-mark"><span class="brand-dot"></span><span class="brand-name">Tormin Group</span></div>

  <div class="person">
    <span class="person-name">Sami Haddad</span>
    <span class="person-dash">–</span>
    <span class="person-title">Managing Partner</span>
  </div>
  <div class="person-contact">+971 (0)50 418 7302 | sami@tormingroup.com | www.tormingroup.com</div>

  <div class="divider"></div>

  <svg width="0" height="0" style="position:absolute">
    <defs>
      <symbol id="icon-phone" viewBox="0 0 20 20">
        <path d="M4 1.5l3 .5 1.2 4-2 1.6c1 2.3 2.8 4.1 5.1 5.2l1.6-2 4 1.2.6 3c-.4 1.5-1.8 2.5-3.4 2.4C7.8 16.9 3.1 12.2 2.6 5.9 2.5 4 3.1 2.3 4 1.5z"/>
      </symbol>
      <symbol id="icon-fax" viewBox="0 0 20 20">
        <rect x="5" y="2" width="10" height="5"/>
        <rect x="1" y="8" width="18" height="7" rx="1"/>
        <rect x="4" y="13" width="12" height="5" fill="#fff" stroke="currentColor"/>
        <rect x="4" y="16" width="12" height="2"/>
      </symbol>
      <symbol id="icon-mail" viewBox="0 0 20 20">
        <path d="M1 4h18v12H1z"/>
        <path d="M1.5 4.5L10 11l8.5-6.5" fill="none" stroke="#fff" stroke-width="1.6"/>
      </symbol>
    </defs>
  </svg>

  <div class="office office--head">
    <p class="office-title">Head office</p>
    <p class="office-address">31480 Abu Dhabi, U.A.E</p>
    <div class="office-line"><svg class="office-icon"><use href="#icon-phone"/></svg>+971 (0)2 5830217</div>
    <div class="office-line"><svg class="office-icon" style="color:var(--brand-red)"><use href="#icon-fax"/></svg>+971 (0)2 5830218</div>
    <div class="office-line"><svg class="office-icon"><use href="#icon-mail"/></svg>sales@tormingroup.com</div>
  </div>

  <div class="office office--dubai">
    <p class="office-title">Dubai Office</p>
    <p class="office-address">274106 Dubai, U.A.E.</p>
    <div class="office-line"><svg class="office-icon"><use href="#icon-phone"/></svg>+971 (0)4 3627045</div>
    <div class="office-line"><svg class="office-icon" style="color:var(--brand-red)"><use href="#icon-fax"/></svg>+971(0)4 3627046</div>
    <div class="office-line"><svg class="office-icon"><use href="#icon-mail"/></svg>sales@tormingroup.com</div>
  </div>

  <div class="office office--qatar">
    <p class="office-title">Qatar Office</p>
    <p class="office-address">20983 Doha, Qatar</p>
    <div class="office-line"><svg class="office-icon"><use href="#icon-phone"/></svg>+974 44713598</div>
    <div class="office-line"><svg class="office-icon" style="color:var(--brand-red)"><use href="#icon-fax"/></svg>+974 44713599</div>
    <div class="office-line"><svg class="office-icon"><use href="#icon-mail"/></svg>sales@tormingroup.com</div>
  </div>
</div>
</body>
</html>
```